Brindle Water - 500ml

to create a water bottle packaging similar to L'onde Claire design. Bottle should be blue similar to PURE FLOW but change the design/logo to Brindle. Wording should be similar just different design and logo. Thanks.

Colors
0054AA
0677BA
7BADD7
CADEEF
E8F1F8

Requirements
Must have
• Bottle must not be in plastic bottles. They are made in a carton instead - see PURE FLOW for reference.

```html
<!DOCTYPE html>
<html lang="en">
<head>
<meta charset="utf-8">
<title>Brindle Water – 500ml carton options</title>
<link rel="stylesheet" href="https://fonts.googleapis.com/css2?family=Montserrat:wght@400;500;600;700;800&family=Kaushan+Script&family=Roboto+Condensed:wght@600&display=swap">
<style>
  :root {
    --bg: #e8e8e8;
    --band: #666666;
    --white: #ffffff;
    --sky: #7badd7;
    --sky-soft: #9ccdef;
    --carton: #4aaee0;
    --navy: #0054aa;
    --royal: #0677d6;
    --text-navy: #0a4f94;
    --snow: #e8f1f8;
    --swatch-1: #ffffff;
    --swatch-2: #9dd1f1;
    --swatch-3: #5ec6f4;
    --swatch-4: #0677d6;
  }
  * { margin: 0; padding: 0; box-sizing: border-box; }
  html, body { width: 1073px; height: 1200px; overflow: hidden; }
  body {
    background: linear-gradient(180deg, #dcdcdc 0%, #f4f4f4 70%, #ffffff 86%);
    font-family: "Montserrat", sans-serif;
    position: relative;
  }
  .carton { position: absolute; top: 240px; width: 293px; height: 757px; }
  .carton--one { left: 170px; }
  .carton--two { left: 606px; }
  .carton svg { display: block; width: 293px; height: 757px; }
  .tagline { font-weight: 400; font-size: 15.5px; letter-spacing: 1.4px; fill: var(--white); font-family: "Montserrat", sans-serif; }
  .brand-name { font-family: "Montserrat", sans-serif; font-weight: 800; font-size: 60px; fill: var(--white); letter-spacing: -1px; }
  .product-type { font-family: "Montserrat", sans-serif; font-weight: 600; font-size: 17px; fill: var(--text-navy); }
  .eco-figure { font-family: "Montserrat", sans-serif; font-weight: 800; font-size: 27px; fill: var(--white); }
  .eco-label { font-family: "Montserrat", sans-serif; font-weight: 500; font-size: 16px; fill: var(--white); letter-spacing: 0.3px; }
  .origin { font-family: "Kaushan Script", cursive; fill: var(--white); }
  .volume { font-family: "Montserrat", sans-serif; font-weight: 400; font-size: 27px; fill: var(--white); }
  .fine-print { font-family: "Roboto Condensed", sans-serif; font-weight: 600; font-size: 8.5px; fill: var(--white); }
  .palette-band { position: absolute; left: 0; top: 1031px; width: 1073px; height: 169px; background: var(--band); }
  .palette { position: absolute; top: 33px; display: flex; }
  .palette--one { left: 198px; gap: 19px; }
  .palette--two { left: 677px; gap: 20px; }
  .swatch { width: 43px; height: 43px; }
  .swatch--white { background: var(--swatch-1); }
  .swatch--pale { background: var(--swatch-2); }
  .swatch--sky { background: var(--swatch-3); }
  .swatch--royal { background: var(--swatch-4); }
  .option-label { position: absolute; top: 98px; width: 240px; text-align: center; color: var(--white); font-weight: 800; font-size: 25px; letter-spacing: 2px; }
  .option-label--one { left: 195px; }
  .option-label--two { left: 640px; }
</style>
</head>
<body>

<div class="carton carton--one">
  <svg viewBox="0 0 293 757" xmlns="http://www.w3.org/2000/svg">
    <defs>
      <linearGradient id="scene-one" x1="0" y1="0" x2="0" y2="1">
        <stop offset="0" stop-color="#4aaee0"/>
        <stop offset="0.5" stop-color="#a9d3ef"/>
        <stop offset="1" stop-color="#4aaee0"/>
      </linearGradient>
    </defs>
    <rect x="0" y="0" width="293" height="757" fill="var(--carton)"/>
    <path d="M0 0 H293 V110 Q146 80 0 100 Z" fill="var(--sky)"/>
    <path d="M0 55 Q146 40 293 70 V110 Q146 80 0 100 Z" fill="var(--sky-soft)" opacity="0.35"/>
    <text class="tagline" x="146.5" y="76" text-anchor="middle">PURE &amp; REFRESHING</text>
    <path d="M0 98 Q146 82 293 112 V252 Q146 212 0 252 Z" fill="var(--royal)"/>
    <path d="M0 98 Q146 82 293 112 V150 Q146 120 0 140 Z" fill="var(--navy)" opacity="0.6"/>
    <path d="M20 234 Q185 210 293 252 V260 Q185 222 20 240 Z" fill="var(--white)"/>
    <text class="brand-name" x="146.5" y="192" text-anchor="middle">Brindle</text>
    <text class="product-type" x="146.5" y="300" text-anchor="middle">Natural Spring Water</text>
    <path d="M146.5 334 C146.5 334 133.5 352 133.5 362 A13 13 0 0 0 159.5 362 C159.5 352 146.5 334 146.5 334 Z" fill="var(--white)"/>
    <path d="M138.5 364 A8 8 0 0 0 154.5 364" fill="none" stroke="var(--carton)" stroke-width="2.5"/>
    <text class="eco-figure" x="146.5" y="406" text-anchor="middle">100%</text>
    <text class="eco-label" x="146.5" y="429" text-anchor="middle">ECO-RESPONSIBLE</text>
    <text class="origin" x="146.5" y="496" text-anchor="middle" font-size="30">Sourced from</text>
    <text class="origin" x="146.5" y="539" text-anchor="middle" font-size="42">the Mountains</text>
    <rect role="img" aria-label="Illustration of snow-capped mountain peaks" x="0" y="555" width="293" height="112" fill="url(#scene-one)"/>
    <text class="volume" x="146.5" y="703" text-anchor="middle">500ml</text>
    <text class="fine-print" x="146.5" y="718" text-anchor="middle">SUSTAINABLY SOURCED WATER</text>
    <text class="fine-print" x="146.5" y="730" text-anchor="middle">IN A PLANT-BASED CARTON</text>
  </svg>
</div>

<div class="carton carton--two">
  <svg viewBox="0 0 293 757" xmlns="http://www.w3.org/2000/svg">
    <defs>
      <linearGradient id="scene-two" x1="0" y1="0" x2="0" y2="1">
        <stop offset="0" stop-color="#4aaee0"/>
        <stop offset="0.5" stop-color="#e8f1f8"/>
        <stop offset="1" stop-color="#4aaee0"/>
      </linearGradient>
    </defs>
    <rect x="0" y="0" width="293" height="757" fill="var(--carton)"/>
    <path d="M0 0 H293 V110 Q146 80 0 100 Z" fill="var(--sky)"/>
    <path d="M0 55 Q146 40 293 70 V110 Q146 80 0 100 Z" fill="var(--sky-soft)" opacity="0.35"/>
    <text class="tagline" x="146.5" y="76" text-anchor="middle">PURE &amp; REFRESHING</text>
    <path d="M0 98 Q146 82 293 112 V252 Q146 212 0 252 Z" fill="var(--royal)"/>
    <path d="M0 98 Q146 82 293 112 V150 Q146 120 0 140 Z" fill="var(--navy)" opacity="0.6"/>
    <path d="M20 234 Q185 210 293 252 V260 Q185 222 20 240 Z" fill="var(--white)"/>
    <text class="brand-name" x="146.5" y="192" text-anchor="middle">Brindle</text>
    <text class="product-type" x="146.5" y="300" text-anchor="middle">Natural Spring Water</text>
    <path d="M146.5 334 C146.5 334 133.5 352 133.5 362 A13 13 0 0 0 159.5 362 C159.5 352 146.5 334 146.5 334 Z" fill="var(--white)"/>
    <path d="M138.5 364 A8 8 0 0 0 154.5 364" fill="none" stroke="var(--carton)" stroke-width="2.5"/>
    <text class="eco-figure" x="146.5" y="406" text-anchor="middle">100%</text>
    <text class="eco-label" x="146.5" y="429" text-anchor="middle">ECO-RESPONSIBLE</text>
    <text class="origin" x="146.5" y="496" text-anchor="middle" font-size="30">Sourced from</text>
    <text class="origin" x="146.5" y="539" text-anchor="middle" font-size="42">the Mountains</text>
    <rect role="img" aria-label="Illustration of white snow-capped mountain peaks above snowy ground" x="0" y="555" width="293" height="112" fill="url(#scene-two)"/>
    <text class="volume" x="146.5" y="703" text-anchor="middle">500ml</text>
    <text class="fine-print" x="146.5" y="718" text-anchor="middle">SUSTAINABLY SOURCED WATER</text>
    <text class="fine-print" x="146.5" y="730" text-anchor="middle">IN A PLANT-BASED CARTON</text>
  </svg>
</div>

<section class="palette-band">
  <div class="palette palette--one">
    <div class="swatch swatch--white"></div>
    <div class="swatch swatch--pale"></div>
    <div class="swatch swatch--sky"></div>
    <div class="swatch swatch--royal"></div>
  </div>
  <div class="option-label option-label--one">OPTION 1</div>
  <div class="palette palette--two">
    <div class="swatch swatch--white"></div>
    <div class="swatch swatch--sky"></div>
    <div class="swatch swatch--royal"></div>
  </div>
  <div class="option-label option-label--two">OPTION 2</div>
</section>

</body>
</html>
```